The Velvet Magpie business card

I need a business card for my makeup artist business. I specialise in bridal, glamour, formal and special occasion makeup.
I am a mobile makeup artist who caters for every from nowra to sydney.
I do the following services:
Bridal makeup
airbrush makeup
special occasion
formals
hens nights/ girls night
makeup lesson
makeup for all ages from flower girl to Nanna of the bride!
photoshoot makeup
SPFX

I would like the card to portray a very professional sleek makeup business. I would also like another version of the card directed especially towards brides.

Please see my website to understand colours etc www.thevelvetmagpie-example.com

The Velvet Magpie
Professional Makeup Artist
Lorraine Kedby
0491802643
info@thevelvetmagpie-example.com
www.thevelvetmagpie-example.com
www.facebook.com/thevelvetmagpie

```html
<!DOCTYPE html>
<html lang="en">
<head>
<meta charset="utf-8">
<title>The Velvet Magpie – Business Card</title>
<link rel="stylesheet" href="https://fonts.googleapis.com/css2?family=Oswald:wght@300;400&family=Open+Sans:wght@400;700&display=swap">
<style>
  :root {
    --page-bg: #e8e5e2;
    --card-white: #ffffff;
    --brand-pink: #e0247f;
    --brand-pink-deep: #c81a6d;
    --soft-pink: #f3b3d4;
    --soft-pink-light: #f9d3e6;
    --swoosh-grey: #6d6d6d;
    --swoosh-light: #bdbdbd;
    --ornament-grey: #ececec;
    --ink: #2c2c2c;
    --band-ink: #3b2431;
  }
  html, body {
    margin: 0;
    width: 1200px;
    height: 913px;
    overflow: hidden;
    background: var(--page-bg);
  }
  .sheet {
    width: 1200px;
    height: 913px;
    display: flex;
    align-items: center;
    justify-content: center;
    gap: 30px;
  }
  .card {
    width: 560px;
    height: 320px;
    border-radius: 14px;
    overflow: hidden;
    position: relative;
    box-shadow: 0 10px 26px rgba(0,0,0,0.18);
    background: var(--card-white);
  }
  .card-art { position: absolute; left: 0; top: 0; display: block; }
  .brand-name {
    position: absolute;
    left: 30px;
    top: 92px;
    margin: 0;
    font-family: "Oswald", sans-serif;
    font-weight: 400;
    font-size: 38px;
    letter-spacing: 2px;
    text-transform: uppercase;
    color: var(--brand-pink);
  }
  .contact-list {
    position: absolute;
    left: 40px;
    top: 166px;
    margin: 0;
    padding: 0;
    list-style: none;
    font-family: "Oswald", sans-serif;
    font-weight: 400;
    font-size: 14px;
    color: var(--ink);
  }
  .contact-list li {
    display: flex;
    align-items: center;
    gap: 9px;
    height: 24px;
  }
  .contact-icon { width: 14px; height: 14px; flex: none; display: block; }
  .owner {
    position: absolute;
    right: 20px;
    top: 195px;
    text-align: left;
    color: #fff;
    font-family: "Open Sans", sans-serif;
  }
  .owner-name { margin: 0; font-weight: 700; font-size: 19px; }
  .owner-title { margin: 2px 0 0; font-weight: 400; font-size: 13px; }
  .photo-strip {
    position: absolute;
    left: 0; top: 0;
    width: 560px; height: 205px;
    display: flex;
  }
  .photo-panel { flex: 1; }
  .photo-panel.bridesmaids { background: linear-gradient(160deg, #3a3f6e, #263078 60%, #e9e4dc); }
  .photo-panel.eye-detail { background: linear-gradient(160deg, #c9c1a4, #e6cdb9 60%, #b89e88); }
  .photo-panel.trial { background: linear-gradient(160deg, #dfe0d8, #e9c9a8 50%, #2d3566); }
  .photo-panel.application { background: linear-gradient(160deg, #b4a593, #f0d9c6 55%, #e7c9b6); }
  .services-band {
    position: absolute;
    left: 0; top: 205px;
    width: 560px; height: 115px;
    background: linear-gradient(180deg, var(--soft-pink), var(--soft-pink-light));
    display: flex;
    align-items: center;
    justify-content: center;
  }
  .services-text {
    margin: 0;
    width: 500px;
    text-align: center;
    font-family: "Open Sans", sans-serif;
    font-weight: 700;
    font-size: 14px;
    line-height: 1.55;
    color: var(--band-ink);
  }
</style>
</head>
<body>
<main class="sheet">

  <section class="card card-front" aria-label="Front of card">
    <svg class="card-art" width="560" height="320" viewBox="0 0 560 320" aria-hidden="true">
      <rect class="corner-ornament" x="420" y="0" width="140" height="40" fill="var(--ornament-grey)" opacity="0.6" role="img" aria-label="Faint swirl ornament area"/>
      <path d="M560,30 C460,50 400,120 350,200 C320,260 270,305 220,320 L560,320 Z" fill="var(--brand-pink)"/>
      <path d="M560,42 C466,64 410,132 362,208 C332,266 288,308 240,320" fill="none" stroke="var(--brand-pink-deep)" stroke-width="3" opacity="0.5"/>
      <path d="M545,26 C445,54 385,128 334,206 C302,266 232,310 150,320" fill="none" stroke="var(--swoosh-grey)" stroke-width="11"/>
      <path d="M520,32 C430,66 368,138 316,212 C280,272 200,314 100,320" fill="none" stroke="var(--swoosh-light)" stroke-width="4"/>
    </svg>

    <h1 class="brand-name">The Velvet Magpie</h1>

    <ul class="contact-list">
      <li>
        <svg class="contact-icon" viewBox="0 0 14 14" aria-hidden="true"><path d="M2,4 Q7,0 12,4 L10,6 Q7,4.5 4,6 Z M3,7 H11 L12,12 H2 Z" fill="var(--brand-pink)"/></svg>
        <span>0491802643</span>
      </li>
      <li>
        <svg class="contact-icon" viewBox="0 0 14 14" aria-hidden="true"><rect x="1" y="3" width="12" height="9" fill="var(--brand-pink)"/><path d="M1,3 L7,8 L13,3" fill="none" stroke="#fff" stroke-width="1.2"/></svg>
        <span>info@thevelvetmagpie-example.com</span>
      </li>
      <li>
        <svg class="contact-icon" viewBox="0 0 14 14" aria-hidden="true"><circle cx="7" cy="7" r="6" fill="var(--brand-pink)"/><path d="M1,7 H13 M7,1 V13 M3,3.5 Q7,5.5 11,3.5 M3,10.5 Q7,8.5 11,10.5" stroke="#fff" stroke-width="0.9" fill="none"/></svg>
        <span>www.thevelvetmagpie-example.com</span>
      </li>
      <li>
        <svg class="contact-icon" viewBox="0 0 14 14" aria-hidden="true"><rect x="1" y="1" width="12" height="12" rx="2" fill="var(--brand-pink)"/></svg>
        <span>/thevelvetmagpie</span>
      </li>
    </ul>

    <div class="owner">
      <p class="owner-name">Lorraine Kedby</p>
      <p class="owner-title">Professional Makeup Artist</p>
    </div>
  </section>

  <section class="card card-back" aria-label="Back of card">
    <div class="photo-strip">
      <div class="photo-panel bridesmaids" role="img" aria-label="Photo of two bridesmaids in navy dresses holding a bouquet"></div>
      <div class="photo-panel eye-detail" role="img" aria-label="Photo of mascara being applied"></div>
      <div class="photo-panel trial" role="img" aria-label="Photo of smiling bridal party after makeup"></div>
      <div class="photo-panel application" role="img" aria-label="Photo of lip makeup being applied"></div>
    </div>
    <div class="services-band">
      <p class="services-text">Bridal makeup • Airbrush makeup • Special occasion • Formals • Hens nights/ Girls night • Makeup lesson • Makeup for all ages from flower girl to Nanna of the bride! • Photoshoot makeup • SPFX</p>
    </div>
  </section>

</main>
</body>
</html>
```